Commercial Loan Originator Business Card (CHANGE COLORS SCHEME)

CHANGE COLOR SCHEME - SAME DESIGN

Name Marlene Agate
Title Commercial Loan Originator
Office (800) 417-2906 x68
Direct (240) 615-2043
Email freshgreens4life@quillbox.example

Name Dale Morrow
Office (800) 417-2906 x70
Direct (410) 392-5184
Email d.morthehomeguy@quillbox.example

Name Leonard Vasko
Office (800) 417-2906 x71
Direct (215) 463-0712
Email l.vasko41@quillbox.example

Name Gwen Halsey
Office (800) 417-2906 x
Direct (202) 548-1370
Email ghalsey63@quillbox.example

Name Mirna Ashby
Office (800) 417-2906 x72
Direct (240) 871-4526
Email tristatehomelending@quillbox.example

```html
<!DOCTYPE html>
<html lang="en">
<head>
<meta charset="utf-8">
<title>Commercial Loan Originator Business Cards</title>
<link href="https://fonts.googleapis.com/css2?family=Montserrat:wght@400;500;700&display=swap" rel="stylesheet">
<style>
  :root {
    --backdrop-top: #cfcfcf;
    --backdrop-bottom: #9c9c9c;
    --card: #ffffff;
    --band: #1b1b1b;
    --accent: #a6ce39;
    --ink: #2b2b2b;
    --photo-a: #8a7f78;
    --photo-b: #4d4540;
  }
  * { margin: 0; padding: 0; box-sizing: border-box; }
  html, body { width: 1200px; height: 1194px; overflow: hidden; }
  body {
    position: relative;
    background: linear-gradient(180deg, var(--backdrop-top), var(--backdrop-bottom));
    font-family: "Montserrat", Arial, sans-serif;
    color: var(--ink);
  }
  .card {
    position: absolute;
    width: 509px;
    height: 291px;
    border-radius: 25px;
    background: var(--card);
    overflow: hidden;
    box-shadow: 4px 6px 10px rgba(0,0,0,0.28);
    --contact-size: 15px;
  }
  .card--long-email { --contact-size: 13px; }
  .card--longest-email { --contact-size: 12.5px; }
  .card__band {
    position: absolute;
    left: 0; top: 0;
    width: 104px; height: 100%;
    background: var(--band);
  }
  .card__photo {
    position: absolute;
    top: 73px;
    left: var(--photo-x);
    width: 146px; height: 146px;
    border-radius: 50%;
    border: 2px solid var(--accent);
    background: radial-gradient(circle at 50% 40%, var(--photo-a), var(--photo-b));
  }
  .card__rule {
    position: absolute;
    left: var(--rule-x);
    top: 76px;
    width: 1.5px; height: 139px;
    background: var(--accent);
  }
  .card__info {
    position: absolute;
    left: calc(var(--rule-x) + 23px);
    right: 14px;
    top: 74px;
  }
  .card__name {
    font-weight: 700;
    font-size: 24px;
    line-height: 1;
    color: var(--accent);
    text-transform: uppercase;
    letter-spacing: 0.2px;
    white-space: nowrap;
  }
  .card__title {
    font-size: 14.5px;
    margin-top: 5px;
    white-space: nowrap;
  }
  .contact { list-style: none; margin-top: 22px; }
  .contact__row {
    display: flex;
    align-items: center;
    gap: 7px;
    font-size: var(--contact-size);
    height: 27.5px;
    white-space: nowrap;
  }
  .contact__icon { width: 11px; height: 11px; fill: var(--accent); flex: none; }
</style>
</head>
<body>

<svg width="0" height="0" style="position:absolute">
  <defs>
    <symbol id="icon-phone" viewBox="0 0 24 24"><path d="M6.6 10.8a15.1 15.1 0 0 0 6.6 6.6l2.2-2.2a1 1 0 0 1 1-.25 11.4 11.4 0 0 0 3.6.57 1 1 0 0 1 1 1V20a1 1 0 0 1-1 1A17 17 0 0 1 3 4a1 1 0 0 1 1-1h3.5a1 1 0 0 1 1 1c0 1.25.2 2.45.57 3.57a1 1 0 0 1-.25 1z"/></symbol>
    <symbol id="icon-mobile" viewBox="0 0 24 24"><path d="M7 1h10a2 2 0 0 1 2 2v18a2 2 0 0 1-2 2H7a2 2 0 0 1-2-2V3a2 2 0 0 1 2-2zm0 3v15h10V4z"/></symbol>
    <symbol id="icon-mail" viewBox="0 0 24 24"><path d="M2 5h20v14H2zm2 2v.5l8 5 8-5V7l-8 5z"/></symbol>
  </defs>
</svg>

<article class="card" style="left:70px;top:95px;--photo-x:52px;--rule-x:227px">
  <div class="card__band"></div>
  <div class="card__photo" role="img" aria-label="Portrait photo of Leonard Vasko"></div>
  <div class="card__rule"></div>
  <div class="card__info">
    <h2 class="card__name">Leonard Vasko</h2>
    <p class="card__title">Commercial Loan Originator</p>
    <ul class="contact">
      <li class="contact__row"><svg class="contact__icon"><use href="#icon-phone"/></svg>(800) 417-2906 x71</li>
      <li class="contact__row"><svg class="contact__icon"><use href="#icon-mobile"/></svg>(215) 463-0712</li>
      <li class="contact__row"><svg class="contact__icon"><use href="#icon-mail"/></svg>l.vasko41@quillbox.example</li>
    </ul>
  </div>
</article>

<article class="card card--long-email" style="left:620px;top:98px;--photo-x:42px;--rule-x:217px">
  <div class="card__band"></div>
  <div class="card__photo" role="img" aria-label="Portrait photo of Marlene Agate" style="--photo-a:#e6d9de;--photo-b:#c8477f"></div>
  <div class="card__rule"></div>
  <div class="card__info">
    <h2 class="card__name">Marlene Agate</h2>
    <p class="card__title">Commercial Loan Originator</p>
    <ul class="contact">
      <li class="contact__row"><svg class="contact__icon"><use href="#icon-phone"/></svg>(800) 417-2906 x68</li>
      <li class="contact__row"><svg class="contact__icon"><use href="#icon-mobile"/></svg>(240) 615-2043</li>
      <li class="contact__row"><svg class="contact__icon"><use href="#icon-mail"/></svg>freshgreens4life@quillbox.example</li>
    </ul>
  </div>
</article>

<article class="card card--long-email" style="left:70px;top:450px;--photo-x:41px;--rule-x:215px">
  <div class="card__band"></div>
  <div class="card__photo" role="img" aria-label="Portrait photo of Dale Morrow" style="--photo-a:#a9a9a6;--photo-b:#4a4c46"></div>
  <div class="card__rule"></div>
  <div class="card__info">
    <h2 class="card__name">Dale Morrow</h2>
    <p class="card__title">Commercial Loan Originator</p>
    <ul class="contact">
      <li class="contact__row"><svg class="contact__icon"><use href="#icon-phone"/></svg>(800) 417-2906 x70</li>
      <li class="contact__row"><svg class="contact__icon"><use href="#icon-mobile"/></svg>(410) 392-5184</li>
      <li class="contact__row"><svg class="contact__icon"><use href="#icon-mail"/></svg>d.morthehomeguy@quillbox.example</li>
    </ul>
  </div>
</article>

<article class="card" style="left:620px;top:453px;--photo-x:42px;--rule-x:217px">
  <div class="card__band"></div>
  <div class="card__photo" role="img" aria-label="Portrait photo of Gwen Halsey" style="--photo-a:#8e7a6c;--photo-b:#5c6e44"></div>
  <div class="card__rule"></div>
  <div class="card__info">
    <h2 class="card__name">Gwen Halsey</h2>
    <p class="card__title">Commercial Loan Originator</p>
    <ul class="contact">
      <li class="contact__row"><svg class="contact__icon"><use href="#icon-phone"/></svg>(800) 417-2906 x</li>
      <li class="contact__row"><svg class="contact__icon"><use href="#icon-mobile"/></svg>(202) 548-1370</li>
      <li class="contact__row"><svg class="contact__icon"><use href="#icon-mail"/></svg>ghalsey63@quillbox.example</li>
    </ul>
  </div>
</article>

<article class="card card--longest-email" style="left:345px;top:807px;--photo-x:32px;--rule-x:205px">
  <div class="card__band"></div>
  <div class="card__photo" role="img" aria-label="Portrait photo of Mirna Ashby" style="--photo-a:#9c8068;--photo-b:#3b2c24"></div>
  <div class="card__rule"></div>
  <div class="card__info">
    <h2 class="card__name">Mirna Ashby</h2>
    <p class="card__title">Commercial Loan Originator</p>
    <ul class="contact">
      <li class="contact__row"><svg class="contact__icon"><use href="#icon-phone"/></svg>(800) 417-2906 x72</li>
      <li class="contact__row"><svg class="contact__icon"><use href="#icon-mobile"/></svg>(240) 871-4526</li>
      <li class="contact__row"><svg class="contact__icon"><use href="#icon-mail"/></svg>tristatehomelending@quillbox.example</li>
    </ul>
  </div>
</article>

</body>
</html>
```